Hop Along Days campaign: promoting kids play in the UK - Website Redesign

Hop Along Days is a national UK campaign that promotes the value of play for children. The current website is live at http://www.hopalongdays.co.uk. This website has been live for 4 years and now needs to be redesigned. The target audience is parents of young children up to the age of 12.

The current site was designed with a series of old adverts in mind. Here is an example of an old advert: http://vidshare.example/qR7tLm2XwZa

Criticisms of existing site:
The design represented the adverts too closely. The result was a website that mirrors the adverts rather than complements them.
The color scheme is too dark.
Text-heavy pages (e.g. http://www.hopalongdays.co.uk/fun.php) are dull and not FUN!

New site
We have recently had a series of new video adverts produced:
advert 1: http://vidshare.example/hB4nVc8JsPe
advert 2: http://vidshare.example/KgW3rTy9DuM
advert 3: http://vidshare.example/zA5oEi1HbNq

The new site should be cleaner and brighter than the existing site, possibly with a white background using graphics, fonts and advert characters (see attached character graphics files) to add the element of fun and play.

The homepage should include:
1. Hop Along Days logo (attached)
2. Social Media links (visible on all pages of the site) – Chatterbook, Chirpline, ClipVault
3. Link to the HopAlongDays app page of the site (visible on all pages)
4. Image/video placeholder that the user can scroll through, view full-size images and play videos.
5. Text area to hold approximately 100 words describing the purpose of the campaign
6. Site footer to contain the same information as on the existing site along with the Northern Games & Crafts Guild logo (attached)

Site structure:
One change to the site structure… the “Brought to you by” menu item will be removed from the top-level menu.

General:
Some pages on the existing site are quite text-heavy, we would like to break up text on these pages in some way. Graphical division of paragraphs, use of advert characters?

Please note that all attached graphics file are the property of the Northern Games & Crafts Guild and must only be used for the purpose of this project.

```html
<!DOCTYPE html>
<html lang="en">
<head>
<meta charset="utf-8">
<title>Hop Along Days – Home</title>
<link href="https://fonts.googleapis.com/css2?family=Oxygen:wght@300;400;700&family=Courier+Prime:wght@700&family=Oswald:wght@400;500&display=swap" rel="stylesheet">
<style>
:root{
  --ink:#3b3b4f;
  --text:#5d5d66;
  --muted:#9a9aa2;
  --navy:#474777;
  --footer:#3a3b52;
  --footer-text:#d9d9e4;
  --orange:#eda200;
  --orange-hot:#f08a00;
  --red:#d32c2c;
  --green:#8bbf22;
  --blue:#3aa3e0;
  --card:#ebe8df;
  --sky:#9fd8ef;
  --grass:#7cc43a;
  --yellow:#f6d400;
  --coral:#ff6f4f;
}
*{box-sizing:border-box;margin:0;padding:0}
html,body{width:672px;height:1200px;overflow:hidden;background:#fff}
body{position:relative;font-family:"Oxygen",Arial,sans-serif;color:var(--text)}
.abs{position:absolute}
h2{font-weight:400}

/* header */
.top-rule{left:0;top:0;width:672px;height:2px;background:linear-gradient(90deg,var(--red),var(--orange),var(--green),var(--blue),var(--navy))}
.brand{left:96px;top:14px;display:flex;align-items:center;gap:6px}
.brand-dot{width:14px;height:14px;border-radius:50%;background:var(--orange-hot)}
.brand-name{font-weight:700;font-size:19px;color:var(--navy);line-height:1}
.social-top{left:520px;top:9px;display:flex;gap:4px}
.social-top span{width:13px;height:13px;border-radius:2px;display:block}
.contact-top{right:106px;text-align:right;font-size:7px;font-weight:700;color:var(--ink)}
.contact-top b{color:var(--red);font-weight:400;font-size:8px}
.contact-top i{color:var(--green);font-style:normal;font-weight:400}
.like-tab{right:0;top:16px;width:21px;height:20px;background:var(--green)}

/* hero */
.hero-side{top:60px;height:244px}
.hero-side.left{left:0;width:96px;background:linear-gradient(180deg,#5f9b3a,#8a6a3e 70%,#e6c98c)}
.hero-side.right{left:573px;width:99px;background:linear-gradient(180deg,#6fa443,#9a7446 70%,#ecd29a)}
.main-nav{left:96px;top:60px;width:477px;height:26px;background:var(--navy);display:flex;justify-content:space-around;align-items:center;font-family:"Courier Prime",monospace;font-size:8px}
.main-nav a{text-decoration:none}
.slide{left:96px;top:86px;width:477px;height:218px;background:linear-gradient(180deg,var(--sky) 0%,#c9ecf7 55%,var(--grass) 70%,#5ea22c 100%)}
.slide-arrow{top:158px;width:27px;height:27px;border-radius:50%;background:rgba(120,120,170,.75)}
.caption{left:96px;top:280px;width:477px;height:24px;display:flex;justify-content:center;align-items:center;gap:7px;color:#fff;font-size:9.5px;font-weight:700;letter-spacing:.2px}
.btn-dark{background:var(--navy);color:#fff;font-size:7px;font-weight:700;padding:4px 9px;border-radius:2px;border:1px solid #6b6b98}
.side-tabs{left:642px;top:126px;width:30px}
.side-tabs span{display:block;height:22px}

/* section heads */
.h-main{color:var(--ink);text-align:center}
.hand-note{font-size:8.5px;color:var(--muted)}

/* how we do it */
.diamond-head{left:170px;width:276px;top:327px;text-align:right}
.diamond-title{font-size:19px;color:var(--ink);line-height:1.1}
.diamond-sub{font-size:7.5px;color:var(--muted);margin-top:1px}
.chair{left:452px;top:318px;width:40px;height:50px;border-radius:8px;background:linear-gradient(180deg,#f5f5f5,#f28fb8)}
.card{top:394px;width:91px;height:126px;background:var(--card);text-align:center;color:var(--ink)}
.card.active{background:var(--orange)}
.card-icon{position:absolute;left:25px;top:-22px;width:41px;height:41px;border-radius:50%;background:#fff;box-shadow:0 1px 2px rgba(0,0,0,.15)}
.card-kicker{position:absolute;top:30px;width:100%;font-size:6.5px}
.card-title{position:absolute;top:39px;width:100%;font-size:10px}
.card-body{position:absolute;top:56px;left:8px;right:8px;font-size:6.3px;line-height:1.45}
.card-go{position:absolute;left:38px;top:102px;width:14px;height:14px;border-radius:50%;background:#fff}
.round-arrow{width:22px;height:22px;border-radius:50%;background:#fff;box-shadow:0 1px 3px rgba(0,0,0,.2)}

/* about */
.about-band{left:0;top:544px;width:672px;height:208px;background:linear-gradient(180deg,#fff,#f2f2f2 50%,#fff)}
.about-title{left:189px;top:571px;font-size:18.5px;color:var(--ink)}
.video{background:#222}
.video-top{position:absolute;left:0;top:0;right:0;height:11px;background:rgba(0,0,0,.7);color:#ddd;font-size:5.5px;padding:2px 5px}
.video-bar{position:absolute;left:0;bottom:0;right:0;height:9px;background:#1a1a1a}
.video-bar::before{content:"";position:absolute;left:4px;right:4px;top:-2px;height:2px;background:#555}
.about-copy{left:337px;top:608px;width:236px;font-size:6.3px;line-height:1.45}
.about-copy p+p{margin-top:6px}
.read-btn{left:337px;top:709px;width:62px;height:16px;background:var(--navy);color:#fff;font-size:7px;font-weight:700;display:flex;align-items:center;justify-content:center;border-radius:2px}

/* videos */
.videos-title{left:0;width:672px;top:780px;font-size:18px}
.thumb-cap{font-size:7.5px;color:var(--ink);text-align:center;width:134px}
.thumb-cap em{display:block;color:var(--red);font-size:7px}
.vsep{top:820px;width:1px;height:100px;background:#e3e3e3}

/* campaign */
.campaign-title{left:102px;top:957px;font-size:18px;color:var(--ink)}
.campaign-copy{left:102px;top:982px;width:326px;font-size:6.3px;line-height:1.45}
.campaign-copy p+p{margin-top:6px}
.campaign-more{left:102px;top:1043px;font-size:7px;color:var(--red);font-style:italic}
.download{left:442px;top:957px;width:135px;height:85px;border-radius:4px;background:linear-gradient(180deg,#e63b3b,#b71717);box-shadow:0 2px 4px rgba(0,0,0,.25)}
.phone{position:absolute;left:9px;top:13px;width:28px;height:61px;border-radius:5px;background:var(--green);border:2px solid #3f6b10}
.phone::after{content:"";position:absolute;left:3px;top:9px;right:3px;bottom:11px;background:#fff}
.dl-title{position:absolute;left:53px;top:7px;font-family:"Oswald",sans-serif;font-size:17px;color:#fff}
.dl-app{position:absolute;left:53px;top:33px;font-size:7px;font-weight:700;color:var(--yellow)}
.dl-text{position:absolute;left:53px;top:43px;width:76px;font-size:6.3px;color:#fff;line-height:1.3}
.dl-link{position:absolute;left:53px;top:67px;font-size:6px;font-weight:700;color:var(--yellow);text-decoration:underline}

/* footer */
.footer{left:0;top:1080px;width:672px;height:120px;background:var(--footer)}
.to-top{left:321px;top:1071px;width:16px;height:16px;border-radius:50%;background:var(--orange)}
.footer-box{left:94px;top:1106px;width:480px;height:70px;border:1px solid #56576e}
.f-head{font-size:7px;font-weight:700;color:#fff}
.f-list{font-size:6.3px;line-height:1.45;color:var(--footer-text)}
.f-org{font-family:"Oswald",sans-serif;color:#fff;text-align:right}
.badge{left:516px;top:1115px;width:46px;height:40px;background:#fff;border-radius:2px}
.copyright{left:0;width:672px;top:1185px;text-align:center;font-size:6.3px;color:var(--footer-text)}
</style>
</head>
<body>

<!-- Header -->
<div class="abs top-rule"></div>
<div class="abs brand">
  <span class="brand-dot"></span><span class="brand-name">Hop Along Days</span>
</div>
<div class="abs social-top" aria-label="Social links">
  <span style="background:var(--navy)" title="Chatterbook"></span>
  <span style="background:var(--blue)" title="Chirpline"></span>
  <span style="background:var(--red)" title="ClipVault"></span>
</div>
<div class="abs contact-top" style="top:29px">CALL : <b>020 555 0147</b></div>
<div class="abs contact-top" style="top:42px">EMAIL : <i>info@hopalongdays.co.uk</i></div>
<div class="abs like-tab"></div>

<!-- Hero -->
<div class="abs hero-side left" role="img" aria-label="Illustrated treehouse and garden fence"></div>
<div class="abs hero-side right" role="img" aria-label="Illustrated wooden play hut"></div>
<nav class="abs main-nav">
  <a style="color:var(--yellow)">Play right now</a>
  <a style="color:var(--green)">Get Involved</a>
  <a style="color:#8fa8ff">Why Play</a>
  <a style="color:var(--coral)">Fun Forever</a>
  <a style="color:var(--orange)">Resources</a>
  <a style="color:#fff">Contact Us</a>
</nav>
<div class="abs slide" role="img" aria-label="Illustrated advert characters playing on a grassy hill under a sky full of flying children"></div>
<div class="abs slide-arrow" style="left:103px">
  <svg width="27" height="27"><path d="M16 8 L10 13.5 L16 19" stroke="#fff" stroke-width="2.5" fill="none"/></svg>
</div>
<div class="abs slide-arrow" style="left:541px">
  <svg width="27" height="27"><path d="M11 8 L17 13.5 L11 19" stroke="#fff" stroke-width="2.5" fill="none"/></svg>
</div>
<div class="abs caption">THE POWER OF KNOWLEDGE. <span class="btn-dark">JOIN US</span></div>
<div class="abs side-tabs" aria-label="Social tabs">
  <span style="background:var(--navy)" title="Chatterbook"></span>
  <span style="background:var(--blue)" title="Chirpline"></span>
  <span style="background:var(--red)" title="ClipVault"></span>
  <span style="background:var(--orange-hot)" title="Feed"></span>
</div>

<!-- How we do it -->
<svg class="abs" style="left:84px;top:330px" width="40" height="46"><path d="M14 2 C0 8 0 28 18 34" stroke="#9a9aa2" fill="none" stroke-width="1"/><path d="M14 30 L19 34 L13 37" stroke="#9a9aa2" fill="none"/></svg>
<div class="abs hand-note" style="left:97px;top:347px">How we do it</div>
<div class="abs diamond-head">
  <h2 class="diamond-title">A child is an uncut Diamond</h2>
  <p class="diamond-sub">Advertising package that is specifically designed to meet your needs</p>
</div>
<div class="abs chair" role="img" aria-label="Toy character sitting in a pink armchair"></div>

<div class="abs round-arrow" style="left:61px;top:449px"><svg width="22" height="22"><path d="M13 7 L9 11 L13 15" stroke="#222" stroke-width="2" fill="none"/></svg></div>
<div class="abs round-arrow" style="left:583px;top:449px"><svg width="22" height="22"><path d="M9 7 L13 11 L9 15" stroke="#222" stroke-width="2" fill="none"/></svg></div>

<div class="abs card" style="left:95px">
  <div class="card-icon"><svg width="41" height="41"><rect x="12" y="14" width="17" height="13" rx="2" fill="var(--green)"/></svg></div>
  <div class="card-kicker">TREASURE</div><div class="card-title">HUNT</div>
  <p class="card-body">Lorem ipsum dolor sit amet, consectetuer adipiscing elit, sed diam ummy nibh ...</p>
  <div class="card-go"><svg width="14" height="14"><path d="M6 4 L9 7 L6 10" stroke="#222" stroke-width="1.5" fill="none"/></svg></div>
</div>
<div class="abs card" style="left:192px">
  <div class="card-icon"><svg width="41" height="41"><circle cx="20.5" cy="20.5" r="9" fill="var(--green)"/></svg></div>
  <div class="card-kicker">EXPAND</div><div class="card-title">OUR MIND</div>
  <p class="card-body">Lorem ipsum dolor sit amet, consectetuer adipiscing elit, sed diam ummy nibh ...</p>
  <div class="card-go"><svg width="14" height="14"><path d="M6 4 L9 7 L6 10" stroke="#222" stroke-width="1.5" fill="none"/></svg></div>
</div>
<div class="abs card active" style="left:289px">
  <div class="card-icon"><svg width="41" height="41"><path d="M20.5 9 L32 30 H9 Z" fill="none" stroke="var(--blue)" stroke-width="2.5" stroke-linejoin="round"/><rect x="19.3" y="16" width="2.4" height="8" fill="var(--blue)"/><circle cx="20.5" cy="27" r="1.3" fill="var(--blue)"/></svg></div>
  <div class="card-kicker">LEARN</div><div class="card-title">ABOUT RISK</div>
  <p class="card-body">Lorem ipsum dolor sit amet, consectetuer adipiscing elit, sed diam ummy nibh ...</p>
  <div class="card-go"><svg width="14" height="14"><path d="M6 4 L9 7 L6 10" stroke="#222" stroke-width="1.5" fill="none"/></svg></div>
</div>
<div class="abs card" style="left:386px">
  <div class="card-icon"><svg width="41" height="41"><path d="M12 10 L22 24" stroke="var(--green)" stroke-width="2"/><circle cx="24" cy="25" r="5" fill="var(--green)"/></svg></div>
  <div class="card-kicker">PLAY</div><div class="card-title">TOGETHER</div>
  <p class="card-body">Lorem ipsum dolor sit amet, consectetuer adipiscing elit, sed diam ummy nibh ...</p>
  <div class="card-go"><svg width="14" height="14"><path d="M6 4 L9 7 L6 10" stroke="#222" stroke-width="1.5" fill="none"/></svg></div>
</div>
<div class="abs card" style="left:482px">
  <div class="card-icon"><svg width="41" height="41"><circle cx="20.5" cy="12" r="3.5" fill="var(--green)"/><circle cx="12" cy="27" r="3.5" fill="var(--green)"/><circle cx="29" cy="27" r="3.5" fill="var(--green)"/><path d="M20.5 16 V21 M12 23 V21 H29 V23" stroke="var(--green)" stroke-width="1.5" fill="none"/></svg></div>
  <div class="card-kicker">LEARN</div><div class="card-title">TO SHARE</div>
  <p class="card-body">Lorem ipsum dolor sit amet, consectetuer adipiscing elit, sed diam ummy nibh ...</p>
  <div class="card-go"><svg width="14" height="14"><path d="M6 4 L9 7 L6 10" stroke="#222" stroke-width="1.5" fill="none"/></svg></div>
</div>

<!-- About -->
<div class="abs about-band"></div>
<svg class="abs" style="left:0;top:540px" width="672" height="8"><path d="M0 4 Q84 0 168 4 T336 4 T504 4 T672 4" stroke="#d4d4d4" stroke-width="1.5" fill="none"/></svg>
<h2 class="abs about-title">Few words about HopAlongDays</h2>
<div class="abs hand-note" style="left:518px;top:579px">What We are</div>
<svg class="abs" style="left:548px;top:562px" width="36" height="46"><path d="M12 2 C34 8 34 30 14 36" stroke="#9a9aa2" fill="none"/><path d="M19 31 L13 36 L19 40" stroke="#9a9aa2" fill="none"/></svg>

<div class="abs video" style="left:96px;top:606px;width:222px;height:125px">
  <div style="position:absolute;inset:0;background:linear-gradient(135deg,#b34a2a,#e0a57a 60%,#6a3a22)" role="img" aria-label="Video still of the campaign ambassador speaking"></div>
  <div class="video-top">New breed of accountants measure</div>
  <div class="video-bar"></div>
</div>
<div class="abs about-copy">
  <p>Hop Along Days Ambassador Dr Helen Marsh explains the importance of engaging children in physical activity and the link with body image. Check out her blog here, read the full report here or check out her top tips here.</p>
  <p>Lorem ipsum dolor sit amet, consectetuer adipiscing elit, sed diam nonummy nibh euismod tincidunt ut laoreet dolore magna aliquam erat volutpat. Ut wisi enim ad minim veniam, dolor sit amet, consectetuer adipiscing elit, sed diam nonummy nibh euismod tincidunt ut laoreet dolore magna aliquam erat volutpat. Ut wisi enim ad minim veniam, dolor sit amet, consectetuer adipiscing elit, sed diam nonummy nibh euismod tincidun.</p>
</div>
<div class="abs read-btn">READ MORE</div>
<svg class="abs" style="left:0;top:748px" width="672" height="8"><path d="M0 4 Q84 0 168 4 T336 4 T504 4 T672 4" stroke="#d4d4d4" stroke-width="1.5" fill="none"/></svg>

<!-- Videos -->
<h2 class="abs h-main videos-title">View Play Videos</h2>
<div class="abs hand-note" style="left:520px;top:799px">All Videos</div>
<svg class="abs" style="left:550px;top:782px" width="36" height="46"><path d="M12 2 C34 8 34 30 14 36" stroke="#9a9aa2" fill="none"/><path d="M19 31 L13 36 L19 40" stroke="#9a9aa2" fill="none"/></svg>

<div class="abs video" style="left:102px;top:832px;width:134px;height:75px">
  <div style="position:absolute;inset:0;background:linear-gradient(180deg,#8fb56a,#4f7d2f)" role="img" aria-label="Video still of a parent and child playing with a cardboard box on grass"></div>
  <div class="video-top" style="font-size:4.5px;height:8px;padding:1px 3px">New breed of accountants measure</div>
  <div class="video-bar" style="height:7px"></div>
</div>
<div class="abs vsep" style="left:251px"></div>
<div class="abs video" style="left:266px;top:832px;width:134px;height:75px">
  <div style="position:absolute;inset:0;background:linear-gradient(180deg,#f1ede6,#d9a9a0)" role="img" aria-label="Video still of a mother and child building with toy blocks"></div>
  <div class="video-top" style="font-size:4.5px;height:8px;padding:1px 3px">New breed of accountants measure</div>
  <div class="video-bar" style="height:7px"></div>
</div>
<div class="abs vsep" style="left:417px"></div>
<div class="abs video" style="left:436px;top:832px;width:134px;height:75px">
  <div style="position:absolute;inset:0;background:linear-gradient(180deg,#e8ddd0,#c7865e)" role="img" aria-label="Video still of toddlers playing together in a nursery"></div>
  <div class="video-top" style="font-size:4.5px;height:8px;padding:1px 3px">New breed of accountants measure</div>
  <div class="video-bar" style="height:7px"></div>
</div>
<div class="abs thumb-cap" style="left:102px;top:914px">How far I can go?<em>- read more</em></div>
<div class="abs thumb-cap" style="left:266px;top:914px">Explore the World.<em>- read more</em></div>
<div class="abs thumb-cap" style="left:436px;top:914px">Learn about risks.<em>- read more</em></div>
<div class="abs round-arrow" style="left:61px;top:894px"><svg width="22" height="22"><path d="M13 7 L9 11 L13 15" stroke="#222" stroke-width="2" fill="none"/></svg></div>
<div class="abs round-arrow" style="left:585px;top:864px"><svg width="22" height="22"><path d="M9 7 L13 11 L9 15" stroke="#222" stroke-width="2" fill="none"/></svg></div>

<!-- Campaign -->
<h2 class="abs campaign-title">Campaign Purpose</h2>
<div class="abs campaign-copy">
  <p>Lorem ipsum dolor sit amet, consectetuer adipiscing elit, sed diam nonummy nibh euismod tincidunt ut laoreet dolore magna aliquam erat volutpat. Ut wisi enim ad minim veniam, Sed ut perspiciatis unde omnis iste natus error sit voluptatem accusantium doloremque laudantium, totam rem aperiam, eaque ipsa quae ab illo inven tore veritatis et quasi architecto beatae vitae dicta sunt explicabo.</p>
  <p>Nemo enim ipsam voluptatem quia voluptas sit aspernatur aut odit aut fugit, sed quia consequuntur magni dolores eos qui ratione voluptatem sequi nesciunt. Neque porro quisquames.</p>
</div>
<div class="abs campaign-more">- read more</div>
<div class="abs download">
  <div class="phone"></div>
  <div class="dl-title">DOWNLOAD</div>
  <div class="dl-app">HopAlongDays App</div>
  <div class="dl-text">Lorem ipsum dolor sits consectetur adipi</div>
  <div class="dl-link">CLICK TO DOWNLOAD</div>
</div>

<!-- Footer -->
<footer class="abs footer"></footer>
<div class="abs to-top"><svg width="16" height="16"><path d="M4.5 9.5 L8 6 L11.5 9.5" stroke="#fff" stroke-width="1.8" fill="none"/></svg></div>
<div class="abs footer-box"></div>
<div class="abs" style="left:114px;top:1102px;width:58px;height:70px;border-left:1px solid #56576e;background:var(--footer)"></div>
<div class="abs f-head" style="left:114px;top:1102px">Quick Links</div>
<div class="abs f-list" style="left:114px;top:1116px">Play Right Now<br>Get Unvolved<br>Why Play<br>Fun Forever<br>Resources<br>Contact Us</div>
<div class="abs f-head" style="left:184px;top:1102px">Contact Us</div>
<div class="abs f-list" style="left:184px;top:1115px">Street no., Street name, City,<br>State, Country. Zip Code.</div>
<svg class="abs" style="left:184px;top:1138px" width="10" height="10"><circle cx="5" cy="5" r="4.3" stroke="#fff" fill="none"/><path d="M3.5 3 Q3.5 6.5 7 6.8" stroke="#fff" stroke-width="1.3" fill="none"/></svg>
<div class="abs f-list" style="left:200px;top:1138px">020-555-0147</div>
<svg class="abs" style="left:184px;top:1153px" width="10" height="10"><rect x="1" y="4" width="8" height="5" rx="1" fill="#fff"/><rect x="2" y="1" width="6" height="3" fill="none" stroke="#fff"/></svg>
<div class="abs f-list" style="left:200px;top:1153px">020-555-0147</div>
<div class="abs f-org" style="right:165px;top:1122px;font-size:10px">© 2014 Northern Games &amp; Crafts Guild Ltd.</div>
<div class="abs f-org" style="right:165px;top:1136px;font-size:9px;font-family:'Oxygen',sans-serif;font-weight:400">14 Alder Lane, Leeds, LS2 7QP</div>
<div class="abs" style="right:165px;top:1148px;font-size:6.5px;color:#fff">Click here to read the disclaimer</div>
<div class="abs badge" role="img" aria-label="Guild membership badge"></div>
<div class="abs copyright">Copyright © 2014. HopAlongDays. All Rights Reserved.</div>

</body>
</html>
```